Create a proposal + product powerpoint

Please see the powerpoint for the slides. There are about 20 slides to be created. Rest of them are for reference and show the design that I like.

I would like to move fast on this, since I need to present it next week (in the week of April 21st).

Please download the current content from here:
https://www.parcelbrook.net/fetch/qRtVmXzLwPkNbYcD

Please make at least 4 slides with the specific content so I can assess your design style.

Target Market(s)

Business Audience and very senior technical audience
Decision Makers

Industry/Entity Type

Product

Colors
e34297
a64599

Requirements
Must have
• Should be very clean, crisp.

I like to use Icons as shown in the powerpoint.... Please see the appendix of the slide deck that shows the various icons. Most of them just have plain text, and I would like to organize so that it does not look like some is just reading text.

I would like to focus on the design aspects so that the audience is clear on how the solution works.

Every page should some graphic element based on the slides shown in the appendix.

```html
<!DOCTYPE html>
<html lang="en">
<head>
<meta charset="UTF-8">
<title>Agenda</title>
<link rel="stylesheet" href="https://fonts.googleapis.com/css2?family=Roboto+Condensed:wght@400&family=Saira+Semi+Condensed:wght@500&display=swap">
<style>
  :root {
    --title-purple: #9a1a9c;
    --bullet-purple: #a3449a;
    --text-dark: #3a3a3a;
    --rule-grey: #d4d4d4;
    --logo-grey: #8a8a8a;
    --band-magenta: #9c1f5e;
    --band-violet: #a651a8;
    --tint-violet: #c455cf;
    --white: #ffffff;
  }
  html, body {
    margin: 0;
    padding: 0;
    overflow: hidden;
    background: var(--white);
  }
  .slide {
    position: relative;
    width: 1200px;
    height: 900px;
    overflow: hidden;
    background: var(--white);
    font-family: "Roboto Condensed", "Arial Narrow", sans-serif;
  }
  .slide-glow {
    position: absolute;
    left: -220px;
    top: 420px;
    width: 700px;
    height: 600px;
    background: radial-gradient(ellipse at 35% 45%, rgba(196, 85, 207, 0.32) 0%, rgba(196, 85, 207, 0.12) 35%, rgba(255, 255, 255, 0) 70%);
  }
  .facet-field {
    position: absolute;
    left: 780px;
    top: 93px;
    width: 420px;
    height: 740px;
    background:
      linear-gradient(90deg, rgba(255,255,255,1) 0%, rgba(255,255,255,0) 55%),
      linear-gradient(160deg, #e9b6ee 0%, #d97fe2 45%, #e3a2ea 75%, #f3d6f5 100%);
  }
  .slide-header {
    position: absolute;
    left: 0;
    top: 0;
    width: 1200px;
    height: 92px;
  }
  .slide-title {
    position: absolute;
    left: 45px;
    top: 8px;
    margin: 0;
    font-family: "Saira Semi Condensed", "Roboto Condensed", sans-serif;
    font-weight: 500;
    font-size: 62px;
    line-height: 74px;
    color: var(--title-purple);
  }
  .header-rule {
    position: absolute;
    left: 42px;
    top: 90px;
    width: 1152px;
    height: 2px;
    background: var(--rule-grey);
  }
  .logo-slot {
    position: absolute;
    left: 1020px;
    top: 12px;
    width: 164px;
    height: 68px;
    border: 2px solid #ececec;
    border-radius: 8px;
    box-sizing: border-box;
    box-shadow: 0 1px 4px rgba(0,0,0,0.08);
    background: var(--white);
    display: flex;
    align-items: center;
    justify-content: center;
    font-family: "Saira Semi Condensed", sans-serif;
    font-weight: 500;
    font-size: 27px;
    letter-spacing: 1px;
    color: var(--logo-grey);
  }
  .agenda-list {
    position: absolute;
    left: 49px;
    top: 142px;
    margin: 0;
    padding: 0;
    list-style: none;
  }
  .agenda-item {
    display: flex;
    align-items: center;
    height: 75px;
    font-size: 40px;
    color: var(--text-dark);
  }
  .agenda-item svg {
    width: 36px;
    height: 36px;
    margin-right: 30px;
    flex: none;
  }
  .slide-footer {
    position: absolute;
    left: 0;
    top: 843px;
    width: 1200px;
    height: 57px;
  }
  .slide-footer svg {
    position: absolute;
    left: 0;
    top: 0;
  }
  .footer-text {
    position: absolute;
    top: 0;
    line-height: 57px;
    font-family: "Saira Semi Condensed", sans-serif;
    font-weight: 500;
    font-size: 24px;
    color: var(--white);
  }
  .page-number { left: 13px; }
  .copyright { right: 15px; }
</style>
</head>
<body>
  <div class="slide">
    <div class="slide-glow"></div>
    <div class="facet-field" role="img" aria-label="Decorative field of overlapping violet triangles fading in from the right edge"></div>

    <header class="slide-header">
      <h1 class="slide-title">Agenda</h1>
      <div class="logo-slot">LOGO HERE</div>
      <div class="header-rule"></div>
    </header>

    <ul class="agenda-list">
      <li class="agenda-item">
        <svg viewBox="0 0 36 36" aria-hidden="true"><circle cx="18" cy="18" r="18" fill="var(--bullet-purple)"/><path d="M14 10 L22 18 L14 26" fill="none" stroke="#fff" stroke-width="4.5" stroke-linecap="round" stroke-linejoin="round"/></svg>
        Trends’ in the market place
      </li>
      <li class="agenda-item">
        <svg viewBox="0 0 36 36" aria-hidden="true"><circle cx="18" cy="18" r="18" fill="var(--bullet-purple)"/><path d="M14 10 L22 18 L14 26" fill="none" stroke="#fff" stroke-width="4.5" stroke-linecap="round" stroke-linejoin="round"/></svg>
        Solution
      </li>
      <li class="agenda-item">
        <svg viewBox="0 0 36 36" aria-hidden="true"><circle cx="18" cy="18" r="18" fill="var(--bullet-purple)"/><path d="M14 10 L22 18 L14 26" fill="none" stroke="#fff" stroke-width="4.5" stroke-linecap="round" stroke-linejoin="round"/></svg>
        Approach to building the solution
      </li>
      <li class="agenda-item">
        <svg viewBox="0 0 36 36" aria-hidden="true"><circle cx="18" cy="18" r="18" fill="var(--bullet-purple)"/><path d="M14 10 L22 18 L14 26" fill="none" stroke="#fff" stroke-width="4.5" stroke-linecap="round" stroke-linejoin="round"/></svg>
        Architecture
      </li>
      <li class="agenda-item">
        <svg viewBox="0 0 36 36" aria-hidden="true"><circle cx="18" cy="18" r="18" fill="var(--bullet-purple)"/><path d="M14 10 L22 18 L14 26" fill="none" stroke="#fff" stroke-width="4.5" stroke-linecap="round" stroke-linejoin="round"/></svg>
        Phasing and Roadmap
      </li>
    </ul>

    <footer class="slide-footer">
      <svg width="1200" height="57" viewBox="0 0 1200 57" aria-hidden="true">
        <polygon points="0,0 906,0 942,57 0,57" fill="var(--band-magenta)"/>
        <polygon points="918,0 1200,0 1200,57 954,57" fill="var(--band-violet)"/>
      </svg>
      <span class="footer-text page-number">Page : 01</span>
      <span class="footer-text copyright">Copyright text here</span>
    </footer>
  </div>
</body>
</html>
```